Membership Based Medical Practice Website

We need a functioning website for a new Membership based medical practice. There will be an enrollment fee and a monthly fee. We would like to see designs that are modern, simple. Should use neutral light colors. Examples of sites we like are www.kellanmoorclinic.com and https://fernholtcare.com/ We also have a link that when "Join Now" is clicked it will go to the signup website.

Target Market(s)

Gay Men, local population, Age group 20 to 60's.

Industry/Entity Type

Medical

Coding

Coded - Design and coding required

Number of Pages Required

5+ page

Font styles to use
Sans Serif

Colors
ffffff
cee9f5
ecf7fb
cfeae6
edf8f6
aaaaaa
e9e9e9
dbdbdb
fff3d1

Requirements
Must have
• Logo and header on every page. Clean, simple design, clear content, mobile compatible.
• Must use Wordpress
Nice to have
• Ideas should come from kellanmoorclinic.com
• Easy to read
Should not have
• Generic patient pictures, bold colors.
• Should not copy from above websites.

```html
<!DOCTYPE html>
<html lang="en">
<head>
<meta charset="utf-8">
<title>Larkmoor Infectious Disease Specialists</title>
<link rel="stylesheet" href="https://fonts.googleapis.com/css2?family=Roboto:wght@400;500;700&family=Roboto+Condensed:wght@400;500;700&family=Open+Sans:wght@400;600&family=Poppins:wght@400;500;600&display=swap">
<style>
:root{
  --white:#ffffff;
  --ink:#2b2b2b;
  --text:#444444;
  --muted:#8a8a8a;
  --sky:#cee9f5;
  --sky-deep:#3d6f8c;
  --band:#d8ecee;
  --band-line:#cfe5e7;
  --gold:#d6b25e;
  --gold-soft:#f1e2b8;
  --cream:#fff3d1;
  --navy:#232c4d;
  --navy-line:#3a4366;
  --card-line:#e9e9e9;
}
*{margin:0;padding:0;box-sizing:border-box}
html,body{width:1200px;height:3774px;overflow:hidden}
body{position:relative;background:var(--white);font-family:"Open Sans",sans-serif;color:var(--text)}
.abs{position:absolute}

/* header */
.site-header{position:absolute;left:0;top:0;width:1200px;height:146px;background:var(--white);z-index:2}
.brand{position:absolute;left:140px;top:14px;width:220px;text-align:center;color:#555}
.brand-dot{width:54px;height:54px;border-radius:50%;border:3px solid var(--gold);margin:0 auto 10px}
.brand-name{font-family:"Roboto",sans-serif;font-weight:400;font-size:14px;letter-spacing:9px;line-height:1.2}
.brand-sub{font-family:"Roboto",sans-serif;font-weight:400;font-size:11px;letter-spacing:.6px;line-height:1.4}
.call{position:absolute;left:650px;top:26px;display:flex;align-items:center;gap:10px}
.call-label{font-family:"Roboto",sans-serif;font-size:17px;color:#555;line-height:1}
.call-num{font-family:"Roboto",sans-serif;font-weight:700;font-size:23px;color:#888;line-height:1.1}
.join{position:absolute;left:898px;top:25px;width:156px;height:44px;background:var(--sky);border-radius:4px;display:flex;align-items:center;justify-content:center;gap:8px;font-family:"Roboto",sans-serif;font-weight:500;font-size:15px;color:var(--sky-deep)}
.nav{position:absolute;right:146px;top:101px;display:flex;gap:28px;font-family:"Roboto",sans-serif;font-weight:500;font-size:17px;color:#333;letter-spacing:.2px}

/* hero */
.hero{position:absolute;left:0;top:146px;width:1200px;height:660px;overflow:hidden}
.hero-photo{position:absolute;inset:0;background:linear-gradient(180deg,#8c9392 0%,#a7adab 28%,#6f7a64 45%,#4f5d3f 58%,#3b3f36 72%,#2b2c2b 100%)}
.hero-title{position:absolute;left:0;top:200px;width:1200px;text-align:center;font-family:"Roboto",sans-serif;font-weight:700;font-size:45px;line-height:58px;color:var(--white);letter-spacing:.5px}
.hero-btn{position:absolute;left:498px;top:350px;width:204px;height:45px;background:var(--sky);border-radius:3px;display:flex;align-items:center;justify-content:center;font-family:"Roboto",sans-serif;font-weight:700;font-size:17px;color:#345}
.hero-arrow{position:absolute;top:260px;width:40px;height:40px;border-radius:50%;display:flex;align-items:center;justify-content:center}
.hero-arrow.left{left:56px}
.hero-arrow.right{left:1106px;background:#333}
.hero-wave{position:absolute;left:0;bottom:0}

/* expertise */
.expertise-title{position:absolute;left:121px;top:898px;font-family:"Roboto",sans-serif;font-weight:500;font-size:24px;line-height:40px;color:var(--ink)}
.cond-list{list-style:none;position:absolute;font-size:13.5px;color:#444}
.cond-list li{display:flex;align-items:center;gap:18px;height:31px}
.plus{width:14px;height:14px;flex:none}
.photo-circle{position:absolute;border-radius:50%;border:4px solid var(--gold)}
.photo-group{left:770px;top:872px;width:312px;height:312px;background:radial-gradient(circle at 50% 35%,#f6d9a3 0%,#e9b46a 35%,#9d6a3d 65%,#4b3526 100%)}
.photo-mug{left:165px;top:2372px;width:342px;height:342px;background:radial-gradient(circle at 50% 45%,#f5f5f2 0%,#d9d6d0 30%,#a1303a 58%,#5b1d24 100%)}
.halo{position:absolute;border-radius:50%;background:radial-gradient(circle,var(--cream) 0%,rgba(255,243,209,0) 70%)}

/* features */
.features{position:absolute;left:0;top:1311px;width:1200px;height:930px;background:var(--band);background-image:repeating-linear-gradient(0deg,rgba(255,255,255,.12) 0 2px,transparent 2px 6px)}
.features-title{position:absolute;left:0;top:75px;width:1200px;text-align:center;font-family:"Roboto",sans-serif;font-weight:500;font-size:27px;line-height:50px;color:var(--ink)}
.card{position:absolute;width:212px;height:282px;background:var(--white);border:1px solid var(--card-line);box-shadow:0 2px 6px rgba(0,0,0,.12);text-align:center}
.card svg.icon{display:block;margin:28px auto 0;width:72px;height:66px}
.card h3{font-family:"Roboto",sans-serif;font-weight:500;font-size:14px;line-height:22px;color:#333;margin-top:16px;letter-spacing:.3px}
.card p{font-size:12px;line-height:22px;color:#555;margin:8px 20px 0}
.card::after{content:"";position:absolute;left:103px;bottom:-3px;width:6px;height:6px;border-radius:50%;background:#888}

/* pricing */
.pricing-title{position:absolute;left:586px;top:2356px;font-family:"Roboto Condensed",sans-serif;font-size:23px;color:var(--ink)}
.pricing-plan{position:absolute;left:586px;top:2406px;font-family:"Roboto",sans-serif;font-weight:500;font-size:19px;line-height:32px;color:var(--ink)}
.perk-list{left:586px;top:2491px}
.perk-list li{font-size:13.5px}
.btn-sky{position:absolute;background:var(--sky);border:1px solid #a9cfe0;border-radius:3px;display:flex;align-items:center;justify-content:center;font-family:"Roboto",sans-serif;font-weight:500;font-size:15px;color:#2f4b5c;box-shadow:0 2px 3px rgba(0,0,0,.12)}

/* call to action */
.cta{position:absolute;left:0;top:2851px;width:1200px;height:500px;background:var(--band);background-image:repeating-linear-gradient(0deg,rgba(255,255,255,.12) 0 2px,transparent 2px 6px)}
.cta-title{position:absolute;left:0;top:80px;width:1200px;text-align:center;font-family:"Roboto",sans-serif;font-weight:500;font-size:29px;color:var(--ink)}
.cta-sub{position:absolute;left:0;top:140px;width:1200px;text-align:center;font-size:18px;color:#333}
.cta-btn{position:absolute;left:458px;top:203px;width:284px;height:44px;background:var(--white);box-shadow:0 2px 5px rgba(0,0,0,.18);display:flex;align-items:center;justify-content:center;font-family:"Roboto",sans-serif;font-weight:700;font-size:17px;color:#222}

/* footer */
.footer-wave{position:absolute;left:0;top:3120px}
.footer{position:absolute;left:0;top:3250px;width:1200px;height:524px;background:var(--navy);color:var(--white);font-family:"Poppins",sans-serif}
.footer h4{position:absolute;top:70px;font-family:"Roboto",sans-serif;font-weight:500;font-size:22px;letter-spacing:.3px}
.contact-item{position:absolute;left:156px;display:flex;gap:20px;font-size:13px;line-height:21px}
.signup-text{position:absolute;left:478px;top:124px;width:390px;font-size:11.5px;line-height:23px}
.email-field{position:absolute;left:478px;top:206px;width:366px;height:38px;border-radius:19px;background:var(--white);overflow:hidden}
.email-field span{position:absolute;left:18px;top:10px;font-size:12px;color:#888}
.email-field b{position:absolute;right:0;top:0;width:118px;height:38px;border-radius:19px;background:var(--sky);color:#23364a;font-weight:600;font-size:13px;display:flex;align-items:center;justify-content:center}
.socials{position:absolute;left:478px;top:260px;display:flex;gap:6px}
.socials i{width:26px;height:26px;border-radius:50%;border:1.5px solid #c8cbd6;display:block}
.quick{position:absolute;left:905px;top:124px;list-style:none;font-size:13px;line-height:25.5px}
.footer-rule{position:absolute;left:0;top:406px;width:1200px;height:1px;background:var(--navy-line)}
.copyright{position:absolute;left:0;top:448px;width:1200px;text-align:center;font-size:14px}
</style>
</head>
<body>

<header class="site-header">
  <div class="brand">
    <div class="brand-dot"></div>
    <div class="brand-name">LARKMOOR</div>
    <div class="brand-sub">INFECTIOUS DISEASE SPECIALISTS</div>
  </div>
  <div class="call">
    <svg width="34" height="34" viewBox="0 0 34 34"><circle cx="17" cy="17" r="15" fill="none" stroke="#999" stroke-width="2"/><path d="M11 9c1-1 2-1 3 0l2 3c.5 1 0 2-1 2.5-.5.3-.5 1 0 2l2.5 2.5c1 .5 1.7.5 2 0 .5-1 1.5-1.5 2.5-1l3 2c1 1 1 2 0 3-2 2-5 2-8-.5l-4-4c-3-3-3.5-6-2-8.5z" fill="#999"/></svg>
    <div><div class="call-label">Call Now</div><div class="call-num">555-014-2290</div></div>
  </div>
  <div class="join">
    <svg width="16" height="16" viewBox="0 0 16 16"><rect x="1.5" y="3" width="11" height="11.5" fill="none" stroke="currentColor" stroke-width="1.6"/><path d="M6 10l1-3 7-6 2 2-7 6z" fill="currentColor"/></svg>
    JOIN US
  </div>
  <nav class="nav"><span>HOME</span><span>SPECIALTIES</span><span>PRICING</span><span>ABOUT US</span><span>FAQ</span><span>BLOG</span></nav>
</header>

<section class="hero">
  <div class="hero-photo" role="img" aria-label="Photo of an open country road running through green fields under a misty grey sky"></div>
  <h1 class="hero-title">SPECIALTY MEDICINE WITH<br>COMMITMENT, COMPASSION AND CARE</h1>
  <div class="hero-btn">GET MORE INFO</div>
  <div class="hero-arrow left"><svg width="14" height="20" viewBox="0 0 14 20"><path d="M11 2L3 10l8 8" fill="none" stroke="#fff" stroke-width="2"/></svg></div>
  <div class="hero-arrow right"><svg width="14" height="20" viewBox="0 0 14 20"><path d="M3 2l8 8-8 8" fill="none" stroke="#fff" stroke-width="2"/></svg></div>
  <svg class="hero-wave" width="1200" height="160" viewBox="0 0 1200 160">
    <path d="M0 110 C200 150 420 150 620 120 C860 85 1050 40 1200 0 L1200 160 L0 160Z" fill="var(--cream)"/>
    <path d="M0 102 C220 145 430 148 640 122 C880 92 1060 60 1200 40 L1200 160 L0 160Z" fill="var(--sky)"/>
    <path d="M0 110 C220 152 430 156 640 130 C880 100 1060 72 1200 58 L1200 160 L0 160Z" fill="var(--white)"/>
  </svg>
</section>

<section class="expertise">
  <h2 class="expertise-title">WE OFFER COMPREHENSIVE TREATMENT<br>OF A WIDE VARIETY OF INFECTIOUS DISEASES.<br>OUT EXPERTISE IS IN THE FOLLOWING AREA.</h2>
  <ul class="cond-list" style="left:121px;top:1039px">
    <li><svg class="plus" viewBox="0 0 14 14"><circle cx="7" cy="7" r="6" fill="none" stroke="#444" stroke-width="1.2"/><path d="M7 4v6M4 7h6" stroke="#444" stroke-width="1.2"/></svg>HIV/PrEP</li>
    <li><svg class="plus" viewBox="0 0 14 14"><circle cx="7" cy="7" r="6" fill="none" stroke="#444" stroke-width="1.2"/><path d="M7 4v6M4 7h6" stroke="#444" stroke-width="1.2"/></svg>Chronic Hepatitis</li>
    <li><svg class="plus" viewBox="0 0 14 14"><circle cx="7" cy="7" r="6" fill="none" stroke="#444" stroke-width="1.2"/><path d="M7 4v6M4 7h6" stroke="#444" stroke-width="1.2"/></svg>Sexually transmitted infections</li>
    <li><svg class="plus" viewBox="0 0 14 14"><circle cx="7" cy="7" r="6" fill="none" stroke="#444" stroke-width="1.2"/><path d="M7 4v6M4 7h6" stroke="#444" stroke-width="1.2"/></svg>Pre-travel vaccinations and counselling</li>
    <li><svg class="plus" viewBox="0 0 14 14"><circle cx="7" cy="7" r="6" fill="none" stroke="#444" stroke-width="1.2"/><path d="M7 4v6M4 7h6" stroke="#444" stroke-width="1.2"/></svg>Infections associated with medical devices</li>
  </ul>
  <ul class="cond-list" style="left:467px;top:1039px">
    <li><svg class="plus" viewBox="0 0 14 14"><circle cx="7" cy="7" r="6" fill="none" stroke="#444" stroke-width="1.2"/><path d="M7 4v6M4 7h6" stroke="#444" stroke-width="1.2"/></svg>Bone and Joint infections</li>
    <li><svg class="plus" viewBox="0 0 14 14"><circle cx="7" cy="7" r="6" fill="none" stroke="#444" stroke-width="1.2"/><path d="M7 4v6M4 7h6" stroke="#444" stroke-width="1.2"/></svg>Postsurgical infections</li>
    <li><svg class="plus" viewBox="0 0 14 14"><circle cx="7" cy="7" r="6" fill="none" stroke="#444" stroke-width="1.2"/><path d="M7 4v6M4 7h6" stroke="#444" stroke-width="1.2"/></svg>Diabetes related infections</li>
    <li><svg class="plus" viewBox="0 0 14 14"><circle cx="7" cy="7" r="6" fill="none" stroke="#444" stroke-width="1.2"/><path d="M7 4v6M4 7h6" stroke="#444" stroke-width="1.2"/></svg>Tuberculosis</li>
  </ul>
  <div class="halo" style="left:716px;top:818px;width:420px;height:420px"></div>
  <div class="photo-circle photo-group" role="img" aria-label="Photo of a group of friends standing arm in arm at sunset"></div>
</section>

<section class="features">
  <h2 class="features-title">LESS WAIT, MORE PERSONAL.<br>WE ARE NOT YOUR TRADITIONAL DOCTOR’S OFFICE</h2>

  <div class="card" style="left:143px;top:216px">
    <svg class="icon" viewBox="0 0 72 66" fill="none" stroke="#9a9a9a" stroke-width="2"><circle cx="36" cy="33" r="27"/><circle cx="36" cy="33" r="21"/><path d="M42 24c-2-2-4-3-6-3-4 0-6 2-6 5 0 7 13 4 13 11 0 3-3 5-7 5-3 0-5-1-7-3M36 17v4M36 42v5"/></svg>
    <h3>STRAIGHTFORWARD<br>PRICING</h3>
    <p>We charge all our patients the same low rate - no surprises.</p>
  </div>
  <div class="card" style="left:377px;top:216px">
    <svg class="icon" viewBox="0 0 72 66" fill="none" stroke="#9a9a9a" stroke-width="2"><rect x="12" y="10" width="44" height="42" rx="2"/><path d="M12 20h44M22 5v10M46 5v10M18 27h6M28 27h6M38 27h6M18 35h6M28 35h6M18 43h6"/><circle cx="52" cy="46" r="11" fill="#fff"/><path d="M52 40v6l4 3"/></svg>
    <h3>AVAILABLE WHEN<br>YOU ARE</h3>
    <p>New patient appointments are available within 1 week.</p>
  </div>
  <div class="card" style="left:610px;top:216px">
    <svg class="icon" viewBox="0 0 72 66" fill="none" stroke="#9a9a9a" stroke-width="2"><path d="M20 36V28a16 16 0 0 1 32 0v8"/><rect x="15" y="32" width="8" height="14" rx="3"/><rect x="49" y="32" width="8" height="14" rx="3"/><path d="M53 46c0 6-6 9-13 9"/><rect x="34" y="52" width="8" height="5" rx="2"/></svg>
    <h3>HASSLE-FREE<br>BOOKING</h3>
    <p>Schedule your appointment online at your convenience - no need to call during business hours.</p>
  </div>
  <div class="card" style="left:843px;top:216px">
    <svg class="icon" viewBox="0 0 72 66" fill="none" stroke="#9a9a9a" stroke-width="2"><path d="M10 10h34v22H24l-8 7v-7h-6z"/><path d="M30 24h32v22h-6v7l-8-7H30z" fill="#fff"/><path d="M36 32h20M36 38h14"/></svg>
    <h3>DEVOTED<br>CARE</h3>
    <p>We schedule enough time at each visit to make sure all of your questions are answered.</p>
  </div>

  <div class="card" style="left:143px;top:538px">
    <svg class="icon" viewBox="0 0 72 66" fill="none" stroke="#9a9a9a" stroke-width="2"><rect x="14" y="16" width="40" height="28" rx="2"/><path d="M8 50h52l-4-6H12z"/><rect x="44" y="6" width="20" height="14" fill="#fff"/><path d="M48 11h12M48 15h8"/></svg>
    <h3>WITHIN<br>YOUR REACH</h3>
    <p>Follow-up appointments may be done by video chat for your convenience.</p>
  </div>
  <div class="card" style="left:377px;top:538px">
    <svg class="icon" viewBox="0 0 72 66" fill="none" stroke="#9a9a9a" stroke-width="2"><ellipse cx="36" cy="34" rx="22" ry="18"/><path d="M41 26c-1-1-3-2-5-2-3 0-5 1-5 4 0 5 10 3 10 8 0 2-2 4-5 4-2 0-4-1-5-2M36 21v3M36 40v4M24 50l-2 8M48 50l2 8"/></svg>
    <h3>SAVE ON<br>LAB COSTS</h3>
    <p>If paying upfront for labs, we offer discounted pricing of up to 90% off standard rates.</p>
  </div>
  <div class="card" style="left:610px;top:538px">
    <svg class="icon" viewBox="0 0 72 66" fill="none" stroke="#9a9a9a" stroke-width="2"><rect x="14" y="26" width="44" height="30" rx="3"/><path d="M30 26v-6h12v6M36 34v14M29 41h14"/><rect x="50" y="8" width="16" height="8" rx="4" transform="rotate(-30 58 12)"/></svg>
    <h3>SAVE<br>ON MEDICATIONS</h3>
    <p>We offer deeply discounted wholesale price medications for our members at pharmacy on site.</p>
  </div>
  <div class="card" style="left:843px;top:538px">
    <svg class="icon" viewBox="0 0 72 66" fill="none" stroke="#9a9a9a" stroke-width="2"><circle cx="36" cy="33" r="26"/><path d="M18 15l36 36"/><rect x="28" y="22" width="16" height="22" rx="2"/></svg>
    <h3>NO<br>MIDDLE MAN</h3>
    <p>We don’t bill any insurance plans so decisions about your healthcare will be made by you.</p>
  </div>
</section>

<section class="pricing">
  <div class="halo" style="left:116px;top:2323px;width:440px;height:440px"></div>
  <div class="photo-circle photo-mug" role="img" aria-label="Photo of an enamel camping mug filled with snow, held in red-gloved hands"></div>
  <h2 class="pricing-title">OUR PRICING IS SIMPLE, TRANSPARENT &amp; AFFORDABLE</h2>
  <p class="pricing-plan">MEMBERSHIP PLAN $80/MO, PLUS A ONE-TIME<br>$99 ENROLLMENT FEE.</p>
  <ul class="cond-list perk-list">
    <li><svg class="plus" viewBox="0 0 14 14"><circle cx="7" cy="7" r="6" fill="none" stroke="#444" stroke-width="1.2"/><path d="M7 4v6M4 7h6" stroke="#444" stroke-width="1.2"/></svg>Includes all appointments, no co-pay</li>
    <li><svg class="plus" viewBox="0 0 14 14"><circle cx="7" cy="7" r="6" fill="none" stroke="#444" stroke-width="1.2"/><path d="M7 4v6M4 7h6" stroke="#444" stroke-width="1.2"/></svg>Relaxed, unrushed visits</li>
    <li><svg class="plus" viewBox="0 0 14 14"><circle cx="7" cy="7" r="6" fill="none" stroke="#444" stroke-width="1.2"/><path d="M7 4v6M4 7h6" stroke="#444" stroke-width="1.2"/></svg>Direct communication with your doctor via phone, email, video chat 24/7</li>
    <li><svg class="plus" viewBox="0 0 14 14"><circle cx="7" cy="7" r="6" fill="none" stroke="#444" stroke-width="1.2"/><path d="M7 4v6M4 7h6" stroke="#444" stroke-width="1.2"/></svg>Convenient online scheduling (no need to call during business hours)</li>
    <li><svg class="plus" viewBox="0 0 14 14"><circle cx="7" cy="7" r="6" fill="none" stroke="#444" stroke-width="1.2"/><path d="M7 4v6M4 7h6" stroke="#444" stroke-width="1.2"/></svg>Wholesale price for labs and medications</li>
  </ul>
  <div class="btn-sky" style="left:589px;top:2682px;width:234px;height:42px">LEARN MORE ABOUT US</div>
</section>

<section class="cta">
  <h2 class="cta-title">READY TO TAKE YOUR HEALTH TO THE NEXT LEVEL?</h2>
  <p class="cta-sub">Sed ut perspiciatis unde omnis iste natus</p>
  <div class="cta-btn">MAKE AN APPOINTMENT</div>
</section>

<svg class="footer-wave" width="1200" height="140" viewBox="0 0 1200 140">
  <path d="M0 30 C260 -10 420 90 700 110 C920 125 1100 60 1200 0 L1200 140 L0 140Z" fill="var(--cream)"/>
  <path d="M0 42 C260 5 420 110 700 125 C930 135 1100 90 1200 40 L1200 140 L0 140Z" fill="var(--navy)"/>
</svg>

<footer class="footer">
  <h4 style="left:156px">CONTACT US</h4>
  <div class="contact-item" style="top:134px">
    <svg width="16" height="22" viewBox="0 0 16 22" fill="none" stroke="#fff" stroke-width="1.4"><path d="M8 21s7-8 7-13A7 7 0 0 0 1 8c0 5 7 13 7 13z"/><circle cx="8" cy="8" r="2.5"/></svg>
    <div>Larkmoor Infectious Disease<br>12 Harrow Lane, Suite 210<br>Fenwick, CO. 80420</div>
  </div>
  <div class="contact-item" style="top:222px">
    <svg width="16" height="18" viewBox="0 0 16 18" fill="none" stroke="#fff" stroke-width="1.4"><path d="M3 1c1-.5 2 0 2.5 1l1.5 3c.3 1-.3 1.5-1 2 .8 2 2.3 3.5 4 4.5.5-.7 1-1.3 2-1l3 1.5c1 .5 1.3 1.5.8 2.5-1.5 3-5 2.5-9-1.5S.5 3 3 1z"/></svg>
    <div>Phone :<br>555-014-2290</div>
  </div>
  <div class="contact-item" style="top:284px">
    <svg width="18" height="14" viewBox="0 0 18 14" fill="none" stroke="#fff" stroke-width="1.4"><rect x="1" y="1" width="16" height="12"/><path d="M1 1l8 7 8-7"/></svg>
    <div>Email :<br>hello@larkmoorid.com</div>
  </div>

  <h4 style="left:478px">SIGN UP TO RECEIVE EMAIL</h4>
  <p class="signup-text">Excepteur sint occaecat cupidatat non proident, sunt in culpa qui officia deserunt mollit anim laborum.</p>
  <div class="email-field"><span>Enter Email</span><b>SUBSCRIBE</b></div>
  <div class="socials"><i></i><i></i><i></i><i></i></div>

  <h4 style="left:901px">QUICK LINKS</h4>
  <ul class="quick"><li>Home</li><li>Specialties</li><li>Pricing</li><li>About Us</li><li>Faq</li><li>Blog</li><li>Join Us</li></ul>

  <div class="footer-rule"></div>
  <p class="copyright">Copyright © Larkmoor Infectious Disease 2019. All rights reserved. | Privacy Policy</p>
</footer>

</body>
</html>
```